Modern Business Card for Larkwell 2018

Our company assumes the best about people. We are creating an online community of entrepreneurs and business leaders who struggle with marketing their business online.

This business card should POP! We recently got a new logo and are launching a new website next month, so our business cards should make a statement that feels:
-Fresh
-Smart
-Trustworthy
-Fun

Target Market(s)

small business owners, entrepreneurs

Industry/Entity Type

Digital Marketing

Contact Information for Business Card

Dimensions: 3.5" x 2"

Font styles to use
Sans Serif

Colors
f37122
ffffff

Requirements
Must have
• We need a business card with a modern, bold design. We will use one side of the card as a lead-generation offer, so text on one side will need to fit up to 140 characters. The business card should stick to our core colors (orange, black, and white).
Nice to have
• We think a vertical "portrait" design could be interesting.
Should not have
• Should not look like a traditional business card. The round icon should stand out from a distance.

```html
<!DOCTYPE html>
<html lang="en">
<head>
<meta charset="utf-8">
<title>Larkwell Business Card</title>
<link href="https://fonts.googleapis.com/css2?family=Open+Sans:wght@400;600;700;800&display=swap" rel="stylesheet">
<style>
  :root {
    --orange: #f37122;
    --orange-deep: #e4601b;
    --ink: #222222;
    --white: #ffffff;
    --panel: #e4e4e4;
    --rule: #6b6b6b;
    --backdrop: #eeeae4;
  }
  * { box-sizing: border-box; margin: 0; padding: 0; }
  html, body {
    width: 1200px; height: 960px; overflow: hidden;
    background: var(--backdrop);
    font-family: "Open Sans", Arial, sans-serif;
  }
  .stage { position: relative; width: 1200px; height: 960px; }

  .card {
    position: absolute; left: 250px; width: 700px; height: 400px;
    border-radius: 4px; overflow: hidden;
    box-shadow: 0 10px 30px rgba(0,0,0,0.18);
  }

  /* Offer side */
  .card--offer { top: 50px; background: linear-gradient(180deg, var(--orange), var(--orange-deep)); color: var(--white); }
  .offer-brand {
    position: absolute; left: 40px; top: 55px; width: 300px; text-align: center;
  }
  .brand-dot {
    width: 42px; height: 42px; border-radius: 50%; background: var(--white);
    margin: 0 auto 10px;
  }
  .brand-name { font-weight: 800; font-size: 46px; letter-spacing: 1px; line-height: 1; }
  .brand-tagline { font-weight: 700; font-size: 12px; letter-spacing: 1.5px; margin-top: 6px; text-transform: uppercase; }
  .offer-divider {
    position: absolute; left: 365px; top: 30px; width: 1px; height: 150px;
    background: rgba(255,255,255,0.55);
  }
  .offer-copy { position: absolute; left: 390px; top: 30px; width: 285px; }
  .offer-headline { font-weight: 800; font-size: 20px; line-height: 1.1; text-transform: uppercase; }
  .offer-body { font-size: 15px; line-height: 1.3; margin-top: 8px; }
  .offer-link { font-weight: 700; font-size: 17px; margin-top: 10px; }
  .writein {
    position: absolute; left: 40px; right: 30px; top: 205px; height: 130px;
    background: var(--panel); border-radius: 18px;
    box-shadow: inset 0 2px 4px rgba(0,0,0,0.15);
  }
  .writein-line { position: absolute; left: 30px; right: 30px; height: 1px; background: var(--rule); }
  .writein-line--1 { top: 42px; }
  .writein-line--2 { top: 86px; }

  /* Contact side */
  .card--contact { top: 510px; background: linear-gradient(180deg, var(--orange), var(--orange-deep)); color: var(--white); }
  .contact-band { position: absolute; left: 0; top: 0; width: 100%; height: 190px; background: var(--ink); text-align: center; }
  .contact-band .brand-name { font-size: 64px; padding-top: 42px; }
  .contact-band .brand-tagline { font-size: 15px; margin-top: 8px; }
  .contact-mark {
    position: absolute; left: 295px; top: 135px; width: 110px; height: 110px;
    border-radius: 50%; background: var(--orange); border: 6px solid var(--white);
  }
  .contact-details { position: absolute; left: 0; top: 262px; width: 100%; text-align: center; }
  .contact-name { font-weight: 800; font-size: 26px; text-transform: uppercase; line-height: 1.15; }
  .contact-role { font-weight: 700; font-size: 19px; text-transform: uppercase; line-height: 1.2; }
  .contact-email { font-size: 19px; line-height: 1.3; }
</style>
</head>
<body>
<main class="stage">
  <section class="card card--offer">
    <div class="offer-brand">
      <div class="brand-dot"></div>
      <div class="brand-name">LARKWELL</div>
      <div class="brand-tagline">Tell stories that inspire action</div>
    </div>
    <div class="offer-divider"></div>
    <div class="offer-copy">
      <p class="offer-headline">Reach more people.<br>Make more money.<br>Create more impact.</p>
      <p class="offer-body">Get your free Larkwell Starter Package and our marketing guide today at</p>
      <p class="offer-link">Larkwellnow.com/start</p>
    </div>
    <div class="writein">
      <div class="writein-line writein-line--1"></div>
      <div class="writein-line writein-line--2"></div>
    </div>
  </section>

  <section class="card card--contact">
    <div class="contact-band">
      <div class="brand-name">LARKWELL</div>
      <div class="brand-tagline">Tell stories that inspire action</div>
    </div>
    <div class="contact-mark"></div>
    <div class="contact-details">
      <p class="contact-name">Dana Morrow</p>
      <p class="contact-role">Story Marketing Coach</p>
      <p class="contact-email">dana@larkwellnow.com</p>
    </div>
  </section>
</main>
</body>
</html>
```